Preliminary design concepts for VELURAN history document

To produce three design concepts as a demonstration for the layout of a document with a look and feel compatible with the existing documents/visual identity of an Australia-based NGO. The design concepts will be used to provide concepts to the NGO and ideally select a designer for the longer 30 - 50 page document.

Target Market(s)

Australian heritage community, international heritage community, general population interested in heritage issues and key stakeholders in heritage projects

Colors
0455a3
3176b5
85acd3
ffc214
fece3e
fee18a
f78f20
f37122

Requirements
Must have
• Eye catching but authoritative design to reflect a serious professional organisation, but one which reflects a modern, progressive approach.
• The designer needs to have experience working with document layout in InDesign and/or Illustrator and provide files in a range of outputs including EPS formats as well as HTML and PDF.
Nice to have
• Interplay between images and design elements

```html
<!DOCTYPE html>
<html lang="en">
<head>
<meta charset="utf-8">
<title>Innovation in conservation – VELURAN design concepts</title>
<link rel="stylesheet" href="https://fonts.googleapis.com/css2?family=Archivo+Black&family=Arimo:ital,wght@0,400;0,700;1,400;1,700&family=Tinos:ital,wght@0,400;0,700;1,400&display=swap">
<style>
  :root {
    --orange: #f37122;
    --orange-deep: #e85c0f;
    --navy: #22307a;
    --blue: #0455a3;
    --yellow: #ffc214;
    --paper: #ffffff;
    --ink: #111111;
    --stage-top: #c4c4c4;
    --stage-bottom: #e6e6e6;
    --photo-dark: #5f5f5f;
    --photo-light: #c9c9c9;
  }
  * { box-sizing: border-box; margin: 0; padding: 0; }
  html, body { width: 1200px; height: 857px; overflow: hidden; background: var(--paper); }
  .board { position: relative; width: 1200px; height: 857px; }
  .board__stage {
    position: absolute; left: 0; top: 0; width: 1200px; height: 442px;
    background: linear-gradient(160deg, var(--stage-bottom), var(--stage-top));
  }

  /* Concept A – orange map cover */
  .cover-map {
    position: absolute; left: 212px; top: 72px; width: 190px; height: 296px;
    background: linear-gradient(140deg, var(--orange), var(--orange-deep));
    border-left: 6px solid var(--navy); overflow: hidden;
  }
  .cover-map__title { position: absolute; left: 42px; top: 58px; font-family: "Archivo Black", sans-serif; font-size: 21px; color: #f4e6da; line-height: 1; }
  .cover-map__sub { position: absolute; left: 62px; top: 80px; font-family: "Arimo", sans-serif; font-style: italic; font-weight: 700; font-size: 15px; color: var(--navy); line-height: 1; }
  .cover-map__kicker { position: absolute; left: 62px; top: 97px; width: 120px; font-family: "Arimo", sans-serif; font-style: italic; font-size: 5px; color: var(--navy); text-transform: uppercase; line-height: 1.4; }
  .cover-map__map { position: absolute; left: 56px; top: 118px; width: 110px; height: 104px; }
  .cover-map__foot { position: absolute; left: 0; bottom: 0; width: 100%; height: 62px; background: #d9d9d9; }
  .brand { display: flex; align-items: center; gap: 3px; font-family: "Arimo", sans-serif; font-weight: 700; color: var(--blue); }
  .cover-map__brand { position: absolute; right: 14px; bottom: 40px; font-size: 7px; }
  .brand__dot { width: 9px; height: 9px; border-radius: 50%; background: var(--blue); }

  /* Concept B – band cover */
  .cover-band { position: absolute; left: 135px; top: 492px; width: 206px; height: 290px; background: var(--orange-deep); overflow: hidden; box-shadow: 0 0 4px rgba(0,0,0,.25); }
  .cover-band__band { position: absolute; left: 0; top: 0; width: 70px; height: 100%; background: var(--navy); }
  .cover-band__title { position: absolute; left: 35px; bottom: 28px; transform-origin: left bottom; transform: rotate(-90deg) translateY(30px); font-family: "Tinos", serif; font-size: 50px; color: var(--paper); white-space: nowrap; line-height: 1; }
  .cover-band__photo { position: absolute; left: 70px; top: 0; width: 136px; height: 100px; background: linear-gradient(180deg, #a9a9a3, #e0e0d8 60%, #bcbcb4); border-bottom: 2px solid var(--paper); }
  .cover-band__sub { position: absolute; left: 74px; top: 112px; font-family: "Tinos", serif; font-size: 13px; color: var(--paper); }
  .cover-band__kicker { position: absolute; left: 76px; top: 131px; width: 125px; font-family: "Arimo", sans-serif; font-style: italic; font-weight: 700; font-size: 6px; color: var(--paper); text-transform: uppercase; line-height: 1.45; }
  .cover-band__badge { position: absolute; left: 76px; top: 150px; width: 56px; height: 24px; background: var(--paper); display: flex; align-items: center; justify-content: center; }
  .cover-band__badge .brand { font-size: 6px; }
  .cover-band__badge .brand__dot { width: 6px; height: 6px; }

  /* Spread */
  .spread { position: absolute; width: 411px; height: 292px; background: var(--paper); box-shadow: 0 0 4px rgba(0,0,0,.25); display: flex; }
  .spread--stage { left: 704px; top: 76px; }
  .spread--flat { left: 676px; top: 490px; }
  .spread__photo { width: 205px; height: 100%; background: linear-gradient(180deg, #e8e8e8 0%, #bdbdbd 35%, var(--photo-dark) 60%, #9a9a9a 85%, var(--photo-light) 100%); }
  .spread__page { position: relative; width: 206px; height: 100%; padding: 36px 20px 0 20px; color: var(--ink); }
  .spread__title { font-family: "Archivo Black", sans-serif; font-size: 11.5px; line-height: 1.05; }
  .spread__quote { margin-top: 9px; font-family: "Tinos", serif; font-style: italic; font-size: 3.6px; line-height: 1.45; }
  .spread__body { position: absolute; left: 20px; top: 104px; width: 126px; column-count: 2; column-gap: 4px; font-family: "Tinos", serif; font-size: 3.6px; line-height: 1.55; text-align: justify; }
  .spread__thumb { position: absolute; left: 150px; top: 104px; width: 37px; height: 29px; background: linear-gradient(180deg, #bfbfbf, #e6e6e6); }
  .spread__caption { position: absolute; left: 150px; top: 136px; width: 40px; font-family: "Arimo", sans-serif; font-weight: 700; font-size: 3px; line-height: 1.4; }
  .spread__landscape { position: absolute; left: 84px; top: 198px; width: 103px; height: 57px; background: linear-gradient(180deg, #eeeeee, #c8c8c8 40%, #4d4d4d 65%, #8a8a8a); }
  .spread__folio { position: absolute; right: 18px; bottom: 26px; font-family: "Arimo", sans-serif; font-weight: 700; font-size: 3.4px; }
</style>
</head>
<body>
<main class="board">
  <div class="board__stage"></div>

  <section class="cover-map" aria-label="Cover concept with map">
    <h1 class="cover-map__title">Innovation</h1>
    <p class="cover-map__sub">in conservation</p>
    <p class="cover-map__kicker">A brief history of Australia VELURAN and the Kellan Charter</p>
    <svg class="cover-map__map" role="img" aria-label="Outline map of Australia" viewBox="0 0 110 104">
      <rect width="110" height="104" fill="var(--orange)" opacity="0.4"/>
    </svg>
    <div class="cover-map__foot"></div>
    <div class="brand cover-map__brand"><span class="brand__dot"></span>VELURAN</div>
  </section>

  <section class="spread spread--stage" aria-label="Introduction spread">
    <div class="spread__photo" role="img" aria-label="Black and white photograph of a ruined stone engine house with a chimney on a hillside"></div>
    <div class="spread__page">
      <h2 class="spread__title">Introduction – what is<br>Australia VELURAN</h2>
      <p class="spread__quote">"The notion of VELURAN is extraordinary. It is international, professional and inter-disciplinary. Its basic tasks are to care for human creations around the world and across time, and to unravel the messages their fabric conveys." (Quote, 1997)</p>
      <p class="spread__body">Australia VELURAN is an incorporated association of professionals working for the conservation and protection of cultural heritage places, including the heritage of buildings, historic cities, cultural landscapes and Indigenous heritage sites. Its mission is to lead cultural heritage conservation in Australia by raising standards, encouraging debate and generating innovative ideas. It plays a strong role in advancing heritage practice in Australia and contributes to heritage practice in the Asia–Pacific region and globally. Its parent body is one of three formal advisory bodies to a global heritage committee of the Global Culture Body. VELURAN is the professional and scientific advisor to that committee on all aspects of cultural heritage. It is one of many national committees associated with the Paris-based international body. Australia VELURAN became an incorporated association in 1984. It now has a membership of over six hundred professionals across a range of disciplines, including architects, historians, archaeologists, town planners, conservators, art historians, geographers, anthropologists, engineers, geologists and lawyers.</p>
      <div class="spread__thumb" role="img" aria-label="Photograph of members standing in arched niches"></div>
      <p class="spread__caption">Australia VELURAN Members at the Old Marrin Hospital, Victoria, 1978</p>
      <div class="spread__landscape" role="img" aria-label="Photograph of a large rock formation in a desert landscape"></div>
      <p class="spread__folio">Kellan Charter | 3</p>
    </div>
  </section>

  <section class="cover-band" aria-label="Cover concept with blue band">
    <div class="cover-band__band"></div>
    <div class="cover-band__photo" role="img" aria-label="Photograph of three members standing in arched stone niches"></div>
    <h1 class="cover-band__title">Innovation</h1>
    <p class="cover-band__sub">in conservation</p>
    <p class="cover-band__kicker">A brief history of Australia VELURAN and the Kellan Charter</p>
    <div class="cover-band__badge"><div class="brand"><span class="brand__dot"></span>VELURAN</div></div>
  </section>

  <section class="spread spread--flat" aria-label="Introduction spread, flat">
    <div class="spread__photo" role="img" aria-label="Black and white photograph of a ruined stone engine house with a chimney on a hillside"></div>
    <div class="spread__page">
      <h2 class="spread__title">Introduction – what is<br>Australia VELURAN</h2>
      <p class="spread__quote">"The notion of VELURAN is extraordinary. It is international, professional and inter-disciplinary. Its basic tasks are to care for human creations around the world and across time, and to unravel the messages their fabric conveys." (Quote, 1997)</p>
      <p class="spread__body">Australia VELURAN is an incorporated association of professionals working for the conservation and protection of cultural heritage places, including the heritage of buildings, historic cities, cultural landscapes and Indigenous heritage sites. Its mission is to lead cultural heritage conservation in Australia by raising standards, encouraging debate and generating innovative ideas. It plays a strong role in advancing heritage practice in Australia and contributes to heritage practice in the Asia–Pacific region and globally. Its parent body is one of three formal advisory bodies to a global heritage committee of the Global Culture Body. VELURAN is the professional and scientific advisor to that committee on all aspects of cultural heritage. It is one of many national committees associated with the Paris-based international body. Australia VELURAN became an incorporated association in 1984. It now has a membership of over six hundred professionals across a range of disciplines, including architects, historians, archaeologists, town planners, conservators, art historians, geographers, anthropologists, engineers, geologists and lawyers.</p>
      <div class="spread__thumb" role="img" aria-label="Photograph of members standing in arched niches"></div>
      <p class="spread__caption">Australia VELURAN Members at the Old Marrin Hospital, Victoria, 1978</p>
      <div class="spread__landscape" role="img" aria-label="Photograph of a large rock formation in a desert landscape"></div>
      <p class="spread__folio">Kellan Charter | 3</p>
    </div>
  </section>
</main>
</body>
</html>
```